Electrician Business Card/ company logo/small business

New Business Cards and logo needed that will catch peoples eye and say we went that extra step. Attached is a design possibly to be incorporated, if u have your own great, lets see it!... This will be a small local business. thank you for all you do!
Halvern Electric
Ned Fosky Owner
Journeyman Electrician
phone 1.555.208.3471
email: KQLHalvernElectric@quellmail.net
call for free estimate!
Updates

Accepted and approved for cards

Target Market(s)

support small local business

Industry/Entity Type

Electrical,

Contact Information for Business Card

name, title,company/ logo, phone, email, free estimate

Other font styles liked:
• easy to read

Colors

Designer to choose colors to be used in the design.

Requirements
Must have
• eye catching everything! logo and halvern electric listed on business card/logo, incorp logo in the background of card
Nice to have
• lightening bolts in eyes or around the triangle? vertical, modern, any design that would be unique and stand out
Should not have
• pinks, reds, yellows,brown

```html
<!DOCTYPE html>
<html lang="en">
<head>
<meta charset="utf-8">
<title>Halvern Electric — Business Card</title>
<link rel="stylesheet" href="https://fonts.googleapis.com/css2?family=Michroma&family=Arimo:wght@400&display=swap">
<style>
  :root {
    --stage: #e9ebee;
    --card-dark: #121314;
    --card-light: #ffffff;
    --blue: #1a8ad8;
    --blue-deep: #0b5fb0;
    --ink: #2a2a2a;
    --rule: #c9c9c9;
  }
  * { box-sizing: border-box; margin: 0; padding: 0; }
  html, body {
    width: 1200px; height: 1015px; overflow: hidden;
    background: var(--stage);
  }
  .stage {
    width: 1200px; height: 1015px;
    display: flex; flex-direction: column; align-items: center; justify-content: center;
    gap: 40px;
  }
  .card {
    width: 760px; height: 434px; position: relative;
    box-shadow: 0 6px 20px rgba(0,0,0,.18);
  }
  .card--back {
    background: var(--card-dark);
    display: flex; align-items: center; justify-content: center;
  }
  .brand {
    display: flex; align-items: center; gap: 18px;
    font-family: "Michroma", sans-serif;
    color: var(--blue);
    text-transform: uppercase;
    line-height: 1.15;
  }
  .brand__dot {
    width: 54px; height: 54px; border-radius: 50%;
    background: var(--blue); flex: none;
  }
  .brand__name { font-size: 34px; letter-spacing: 1px; }
  .card--front { background: var(--card-light); }
  .card--front .brand {
    position: absolute; top: 56px; right: 52px;
  }
  .card--front .brand__name { font-size: 28px; }
  .card--front .brand__dot { width: 44px; height: 44px; }
  .rule {
    position: absolute; height: 1px; background: var(--rule);
  }
  .rule--top { left: 300px; right: 40px; top: 176px; }
  .rule--mid { left: 60px; right: 330px; top: 300px; }
  .person {
    position: absolute; left: 60px; top: 222px;
  }
  .person__name {
    font-family: "Michroma", sans-serif; color: var(--blue);
    font-size: 30px; text-transform: uppercase; letter-spacing: 1px;
  }
  .person__title {
    font-family: "Arimo", sans-serif; color: var(--ink);
    font-size: 22px; margin-top: 4px;
  }
  .contact {
    position: absolute; left: 60px; top: 322px;
    list-style: none;
    font-family: "Arimo", sans-serif; color: var(--ink); font-size: 22px;
  }
  .contact li { display: flex; align-items: center; gap: 14px; height: 34px; }
  .contact svg { width: 22px; height: 22px; flex: none; }
  .web {
    position: absolute; right: 40px; top: 268px;
    font-family: "Arimo", sans-serif; font-size: 20px; color: var(--blue);
  }
  .web span { color: var(--blue-deep); }
</style>
</head>
<body>
<main class="stage">
  <section class="card card--back" aria-label="Card back">
    <div class="brand">
      <span class="brand__dot"></span>
      <span class="brand__name">Halvern<br>Electric</span>
    </div>
  </section>

  <section class="card card--front" aria-label="Card front">
    <div class="brand">
      <span class="brand__dot"></span>
      <span class="brand__name">Halvern<br>Electric</span>
    </div>
    <div class="rule rule--top"></div>

    <div class="person">
      <p class="person__name">Ned Fosky</p>
      <p class="person__title">Journeyman Electrician</p>
    </div>
    <p class="web"><span>www.</span>halvernwire.net</p>
    <div class="rule rule--mid"></div>

    <ul class="contact">
      <li>
        <svg viewBox="0 0 24 24" aria-hidden="true"><path fill="var(--blue)" d="M6.6 10.8a15.1 15.1 0 0 0 6.6 6.6l2.2-2.2c.3-.3.7-.4 1-.2 1.1.4 2.3.6 3.6.6.6 0 1 .4 1 1V20c0 .6-.4 1-1 1A17 17 0 0 1 3 4c0-.6.4-1 1-1h3.5c.6 0 1 .4 1 1 0 1.3.2 2.5.6 3.6.1.3 0 .7-.2 1z"/></svg>
        1.555.208.3471
      </li>
      <li>
        <svg viewBox="0 0 24 24" aria-hidden="true"><rect x="2" y="5" width="20" height="14" fill="var(--blue)"/><path d="M2 5l10 8 10-8" fill="none" stroke="#fff" stroke-width="1.6"/></svg>
        KQLHalvernElectric@quellmail.net
      </li>
    </ul>
  </section>
</main>
</body>
</html>
```